BildeVOLD buisnesscard

Hey :) I need a modern buisnesscard for my company BildeVOLD
It most have:
Dagligleder og Fotograf: Henrik Audun Strandvik

Mob: +4791264085
Epost: post@bildevold.example
Adresse: Kvernbakken9, 6040 Fjordvik

Facbook and instagram logo with text BildeVOLD

BildeVOLD logo

It Company

```html
<!DOCTYPE html>
<html lang="no">
<head>
<meta charset="utf-8">
<title>BildeVOLD – visittkort</title>
<link rel="stylesheet" href="https://fonts.googleapis.com/css2?family=Open+Sans:wght@400;700&display=swap">
<style>
  :root {
    --ink: #000000;
    --paper: #ffffff;
    --steel: #a6a6a6;
    --backdrop: #d9d9d9;
  }
  * { box-sizing: border-box; margin: 0; padding: 0; }
  html, body { width: 1200px; height: 997px; overflow: hidden; }
  body {
    background: var(--backdrop);
    font-family: "Open Sans", sans-serif;
    display: flex;
    flex-direction: column;
    align-items: center;
    justify-content: center;
    gap: 50px;
  }
  .card {
    position: relative;
    width: 740px;
    height: 423px;
    overflow: hidden;
  }

  /* Front */
  .card--front { background: var(--paper); color: var(--ink); }
  .card--front .band-top { position: absolute; top: 0; left: 0; right: 0; height: 14px; background: var(--ink); }
  .card--front .band-bottom { position: absolute; bottom: 0; left: 0; right: 0; height: 14px; background: var(--steel); }

  .holder { position: absolute; left: 42px; bottom: 78px; }
  .holder__name { font-weight: 700; font-size: 25px; line-height: 1.2; }
  .holder__role { font-size: 23px; line-height: 1.25; }

  .contact { position: absolute; left: 438px; top: 40px; right: 0; font-size: 19px; }
  .contact__row { display: flex; align-items: center; gap: 8px; height: 30px; white-space: nowrap; }
  .contact__icon { width: 22px; height: 22px; flex: none; }

  .address {
    margin: 26px 0 0 50px;
    background: var(--ink);
    color: var(--paper);
    padding: 10px 14px;
    display: flex;
    gap: 8px;
    align-items: flex-start;
    font-size: 19px;
    line-height: 1.3;
    white-space: nowrap;
  }
  .address .contact__icon { margin-top: 2px; }

  .social { margin: 22px 0 0 140px; }
  .social__mark { width: 26px; height: 26px; background: var(--ink); border-radius: 4px; flex: none; }

  /* Back */
  .card--back { background: var(--ink); }
  .card--back .band-top { position: absolute; top: 0; left: 0; right: 0; height: 16px; background: var(--steel); }
  .card--back .band-bottom { position: absolute; bottom: 0; left: 0; right: 0; height: 16px; background: var(--steel); }
  .brand {
    position: absolute; inset: 0;
    display: flex; align-items: center; justify-content: center; gap: 18px;
    color: var(--steel);
  }
  .brand__square { width: 64px; height: 64px; background: var(--steel); }
  .brand__name { font-weight: 700; font-size: 50px; letter-spacing: 0.5px; }
</style>
</head>
<body>

<section class="card card--front">
  <div class="band-top"></div>

  <div class="contact">
    <div class="contact__row">
      <svg class="contact__icon" viewBox="0 0 22 22" aria-hidden="true">
        <circle cx="11" cy="11" r="11" fill="#000"/>
        <path d="M7.5 6 l2 0 1 3 -1.4 1 a6 6 0 0 0 3 3 l1-1.4 3 1 0 2 a1.5 1.5 0 0 1 -1.5 1.5 A8.5 8.5 0 0 1 6 7.5 A1.5 1.5 0 0 1 7.5 6z" fill="#fff"/>
      </svg>
      <span>+4791264085</span>
    </div>
    <div class="contact__row">
      <svg class="contact__icon" viewBox="0 0 22 22" aria-hidden="true">
        <circle cx="11" cy="11" r="11" fill="#000"/>
        <rect x="5.5" y="7" width="11" height="8" fill="none" stroke="#fff" stroke-width="1.4"/>
        <path d="M5.5 7 L11 11.5 L16.5 7" fill="none" stroke="#fff" stroke-width="1.4"/>
      </svg>
      <span>post@bildevold.example</span>
    </div>

    <div class="address">
      <svg class="contact__icon" viewBox="0 0 22 22" aria-hidden="true">
        <path d="M11 2 a6.5 6.5 0 0 1 6.5 6.5 C17.5 13 11 20 11 20 S4.5 13 4.5 8.5 A6.5 6.5 0 0 1 11 2z" fill="#fff"/>
        <circle cx="11" cy="8.5" r="2.4" fill="#000"/>
      </svg>
      <div>Kvernbakken9<br>6040 Fjordvik, Nordhav</div>
    </div>

    <div class="social">
      <div class="contact__row"><span class="social__mark"></span><span>BildeVOLD</span></div>
      <div class="contact__row" style="margin-top:6px"><span class="social__mark"></span><span>BildeVOLD</span></div>
    </div>
  </div>

  <div class="holder">
    <p class="holder__name">Henrik Audun Strandvik</p>
    <p class="holder__role">Dagligleder og Fotograf</p>
  </div>

  <div class="band-bottom"></div>
</section>

<section class="card card--back">
  <div class="band-top"></div>
  <div class="brand">
    <span class="brand__square"></span>
    <span class="brand__name">BildeVOLD</span>
  </div>
  <div class="band-bottom"></div>
</section>

</body>
</html>
```